Under Morning Lantern website

I need a website to sell my t-shirt designs. I have around 5 designs I plan to sell on my initial launch, but only 3 photos at the moment. I would love a main page with the product images below maybe a large nicely designed header image, showing products with their sizes, item name/description, a way to add to cart and a review system like stars below each product image. Maybe a share option to Photo Wall, Circle, Chirp, Pinboard, etc. would be cool too. Also on the main page under the product images a section showcasing my Photo Wall photos for the company. Then a section where I will include an About Me video from like Reelbox. Lastly, on the main page an option to join my Mailing List at the footer with links to my Circle and Photo Wall social accounts, links to pages (About Me, Shop, Photo Wall page, & Contact Us) as well as Track Order.

The other 4 pages will be for an About Me, which is the video I will make later that will be from Reelbox. Then the Shop page. Then the Photo Wall page showcasing all the photos I plan to use to market the products, and a Contact Us Page.

I plan to possibly connect this to Stallfront, so showcasing payment options (Palo, Birch Pay, Wayfarer, etc.) would be nice.

Lastly, I don't plan on doing returns/exchanges so maybe an area showing that would be nice too. ALL SALES FINAL

Mobile Friendly!

1st image is logo and other 4 images are t-shirt designs

Coded - Design and coding required

5+ page

• Separate pages, No Refunds (All Sales Final), Add to Cart, Way to Purchase

```html
<!DOCTYPE html>
<html lang="en">
<head>
<meta charset="utf-8">
<title>Under Morning Lantern – Shop</title>
<link href="https://fonts.googleapis.com/css2?family=Open+Sans:wght@400;600;700&display=swap" rel="stylesheet">
<style>
:root{
  --board:#e9e9e9;
  --ink:#222;
  --muted:#8a8a8a;
  --line:#e2e2e2;
  --white:#fff;
  --dark:#111;
  --accent:#2bb3c0;
  --shirt-white:#f1f1f1;
  --shirt-purple:#7a4fc9;
  --shirt-teal:#33c1b6;
  --shirt-yellow:#f4c319;
  --shirt-orange:#f0642e;
}
*{box-sizing:border-box;margin:0;padding:0}
html,body{width:793px;height:1200px;overflow:hidden}
body{background:var(--board);font-family:"Open Sans",Arial,sans-serif;color:var(--ink);position:relative}
.page{position:absolute;top:30px;width:350px;height:1135px;background:var(--white);overflow:hidden;box-shadow:0 3px 14px rgba(0,0,0,.25)}
.page--home{left:30px}
.page--login{left:413px}

.hero{height:222px;background:linear-gradient(100deg,#1c1d20 0%,#3a3c40 55%,#23252a 100%);position:relative;color:var(--white)}
.nav{display:flex;justify-content:space-between;align-items:center;padding:8px 14px}
.brand{display:flex;align-items:center;gap:4px;font-weight:700;font-size:10px;color:var(--accent);letter-spacing:1px}
.brand i{width:6px;height:6px;background:var(--accent);display:block}
.nav ul{display:flex;gap:9px;list-style:none;font-size:4.5px;color:#ddd}
.hero-copy{position:absolute;left:16px;top:88px}
.hero-copy h1{font-size:15px;font-weight:600}
.hero-copy p{font-size:4.5px;color:#ccc;margin:4px 0 6px;width:110px;line-height:1.5}
.btn{display:inline-block;background:var(--dark);color:var(--white);font-size:4.5px;padding:3px 9px;border:1px solid #555}
.btn--light{background:var(--white);color:var(--ink);border-color:var(--white)}

.best{height:150px;padding-top:16px;text-align:center}
.section-title{font-size:6px;font-weight:600;margin-bottom:9px}
.shirts{display:flex;justify-content:center;gap:10px}
.shirt{width:50px}
.shirt-img{height:64px}
.shirt p{font-size:4px;color:var(--muted);margin-top:4px;line-height:1.4}
.stars{color:#f0b400;font-size:4.5px;letter-spacing:.5px}

.banner{height:130px;background:linear-gradient(90deg,#8d9096,#b9bcc0 60%,#9ea1a6);position:relative}
.banner-copy{position:absolute;left:150px;top:48px;color:var(--white)}
.banner-copy h3{font-size:6px;font-weight:600}
.banner-copy p{font-size:4px;margin:3px 0 6px;width:110px;line-height:1.5}

.features{height:68px;display:flex;justify-content:space-around;align-items:center;padding:0 20px}
.feature{text-align:center;width:60px}
.feature svg{width:10px;height:10px;stroke:var(--ink);fill:none;stroke-width:1.3}
.feature b{display:block;font-size:4.5px;font-weight:600;margin-top:2px}
.feature span{font-size:3.8px;color:var(--muted)}

.video{height:142px;background:linear-gradient(100deg,#c9b9a3,#7b6a5a 50%,#3a3a3c);position:relative}
.about-card{position:absolute;left:12px;top:40px;width:110px;background:var(--white);padding:8px}
.about-card h3{font-size:6px;font-weight:600}
.about-card p{font-size:3.8px;color:var(--muted);line-height:1.5;margin:3px 0 6px}
.play{position:absolute;left:240px;top:58px;width:24px;height:24px;border-radius:50%;background:var(--white)}
.play svg{width:24px;height:24px}

.product{height:150px;display:flex;padding:18px 30px;gap:20px;position:relative}
.arrow{position:absolute;top:70px;font-size:8px;color:var(--muted)}
.product-img{width:100px;height:110px;background:linear-gradient(#f4f4f4,#e8e8e8);display:flex;align-items:center;justify-content:center}
.product-img div{width:62px;height:72px;background:var(--dark)}
.details h3{font-size:7px;font-weight:600}
.price{font-size:5px;margin:2px 0}
.details p{font-size:3.8px;color:var(--muted);line-height:1.5;width:120px}
.sizes{display:flex;gap:3px;margin:5px 0}
.sizes span{font-size:4px;border:1px solid var(--line);padding:1px 3px}
.qty{display:flex;gap:4px;align-items:center;margin-bottom:5px}
.qty span{font-size:4px;border:1px solid var(--line);padding:1px 5px}
.btn--wide{padding:3px 22px}
.share{display:flex;gap:3px;margin-top:6px;align-items:center;font-size:4px;color:var(--muted)}
.share i{width:5px;height:5px;border-radius:50%;background:#555;display:block}

.insta{height:110px;display:flex;justify-content:center;gap:8px;padding-top:6px}
.insta-item{width:56px}
.insta-img{height:58px}
.insta-item p{font-size:3.8px;color:var(--muted);margin-top:3px;line-height:1.4}

.footer{padding:8px 20px;border-top:1px solid var(--line);height:157px}
.footer-cols{display:flex;gap:26px}
.footer-cols .brand{font-size:11px}
.footer-cols h4{font-size:4.5px;font-weight:600;margin-bottom:3px}
.footer-cols li{list-style:none;font-size:3.8px;color:var(--muted);line-height:1.8}
.signup{display:flex;margin-top:3px}
.signup span{border:1px solid var(--line);font-size:3.6px;color:var(--muted);padding:2px 4px;width:50px}
.signup b{background:var(--dark);color:var(--white);font-size:3.6px;padding:2px 4px}
.social{display:flex;justify-content:center;gap:5px;margin-top:26px}
.social i{width:6px;height:6px;border-radius:50%;background:#333;display:block}
.payments{display:flex;justify-content:center;gap:6px;margin-top:8px;font-size:4px;font-weight:600;color:#444}
.final{text-align:center;font-size:3.8px;color:var(--muted);margin-top:6px}

.overlay{position:absolute;inset:0;background:rgba(25,25,25,.62)}
.login{position:absolute;top:95px;left:45px;width:270px;background:var(--white);padding:10px 12px}
.login h2{font-size:8px;font-weight:600;margin-bottom:6px}
.login label{display:block;font-size:4px;color:var(--muted)}
.field{height:8px;border:1px solid #ccc;margin:2px 0 5px}
.login .btn{margin-top:2px}
.login p{font-size:3.8px;color:var(--muted);margin-top:5px}
</style>
</head>
<body>

<div class="page page--home">
  <header class="hero" role="img" aria-label="Header photo: man in a dark printed tee">
    <nav class="nav"><div class="brand"><i></i>UML</div>
      <ul><li>Home</li><li>Shop</li><li>About Me</li><li>Photo Wall</li><li>Contact Us</li><li>Cart</li></ul></nav>
    <div class="hero-copy"><h1>Under Morning Lantern</h1><p>Faith-made tees for every day. Wear your light with bold designs and soft fabric.</p><span class="btn">Shop Now</span></div>
  </header>
  <section class="best">
    <h2 class="section-title">Best Sellers</h2>
    <div class="shirts">
      <div class="shirt"><div class="shirt-img" role="img" aria-label="White tee" style="background:var(--shirt-white)"></div><p>Lantern Tee<br>$24.00</p><div class="stars">★★★★★</div></div>
      <div class="shirt"><div class="shirt-img" role="img" aria-label="Purple tee" style="background:var(--shirt-purple)"></div><p>Dawn Tee<br>$24.00</p><div class="stars">★★★★★</div></div>
      <div class="shirt"><div class="shirt-img" role="img" aria-label="Teal tee" style="background:var(--shirt-teal)"></div><p>Morning Tee<br>$24.00</p><div class="stars">★★★★★</div></div>
      <div class="shirt"><div class="shirt-img" role="img" aria-label="Yellow tee" style="background:var(--shirt-yellow)"></div><p>Glow Tee<br>$24.00</p><div class="stars">★★★★★</div></div>
      <div class="shirt"><div class="shirt-img" role="img" aria-label="Orange tee" style="background:var(--shirt-orange)"></div><p>Ember Tee<br>$24.00</p><div class="stars">★★★★★</div></div>
    </div>
  </section>
  <section class="banner" role="img" aria-label="Photo: man wearing a teal tee">
    <div class="banner-copy"><h3>New Designs Every Season</h3><p>Fresh prints made to share the message with a bold look.</p><span class="btn btn--light">Shop Now</span></div>
  </section>
  <section class="features">
    <div class="feature"><svg viewBox="0 0 10 10"><rect x="1" y="3" width="5" height="4"/><path d="M6 4h2l1 2v1H6"/></svg><b>Fast Shipping</b><span>Ships in 3 days</span></div>
    <div class="feature"><svg viewBox="0 0 10 10"><circle cx="5" cy="5" r="4"/><path d="M3 5l1.5 1.5L7 4"/></svg><b>Quality Cotton</b><span>Soft and durable</span></div>
    <div class="feature"><svg viewBox="0 0 10 10"><circle cx="5" cy="5" r="4"/><path d="M5 3v2l1.5 1"/></svg><b>All Sales Final</b><span>No returns</span></div>
    <div class="feature"><svg viewBox="0 0 10 10"><rect x="1.5" y="2.5" width="7" height="5"/><path d="M1.5 4h7"/></svg><b>Secure Payment</b><span>Safe checkout</span></div>
  </section>
  <section class="video" role="img" aria-label="Video still: man in a black printed tee">
    <div class="about-card"><h3>About Me</h3><p>A short story about why these shirts were made and the hope behind each design.</p><span class="btn">Watch Video</span></div>
    <div class="play"><svg viewBox="0 0 24 24"><path d="M10 7l7 5-7 5z" fill="#222"/></svg></div>
  </section>
  <section class="product">
    <span class="arrow" style="left:12px">‹</span><span class="arrow" style="right:12px">›</span>
    <div class="product-img"><div role="img" aria-label="Black tee with print"></div></div>
    <div class="details"><h3>Black T-Shirt</h3><div class="price">$24.00</div><div class="stars">★★★★★</div>
      <p>Soft cotton tee with our lantern print. Unisex fit, made to last.</p>
      <div class="sizes"><span>S</span><span>M</span><span>L</span><span>XL</span><span>2XL</span></div>
      <div class="qty"><span>- 1 +</span></div><span class="btn btn--wide">Add to Cart</span>
      <div class="share">Share <i></i><i></i><i></i><i></i></div></div>
  </section>
  <section class="insta">
    <div class="insta-item"><div class="insta-img" role="img" aria-label="Photo wall post: man in tee" style="background:#6b6f74"></div><p>Sunday best in black.</p></div>
    <div class="insta-item"><div class="insta-img" role="img" aria-label="Photo wall post: teal tee" style="background:#4f8b92"></div><p>Teal for the summer.</p></div>
    <div class="insta-item"><div class="insta-img" role="img" aria-label="Photo wall post: grey tee" style="background:#8a8d90"></div><p>Grey on the go.</p></div>
    <div class="insta-item"><div class="insta-img" role="img" aria-label="Photo wall post: red tee" style="background:#b8574a"></div><p>New ember drop.</p></div>
  </section>
  <footer class="footer">
    <div class="footer-cols"><div class="brand"><i></i>UML</div>
      <div><h4>Pages</h4><ul><li>About Me</li><li>Shop</li><li>Photo Wall</li><li>Contact Us</li></ul></div>
      <div><h4>Help</h4><ul><li>Track Order</li><li>Shipping</li><li>All Sales Final</li></ul></div>
      <div><h4>Mailing List</h4><div class="signup"><span>Your email</span><b>Join</b></div></div></div>
    <div class="social"><i></i><i></i><i></i></div>
    <div class="payments"><span>Palo</span><span>Birch Pay</span><span>Wayfarer</span></div>
    <p class="final">© Under Morning Lantern. All sales final.</p>
  </footer>
</div>

<div class="page page--login">
  <header class="hero" role="img" aria-label="Header photo: man in a dark printed tee">
    <nav class="nav"><div class="brand"><i></i>UML</div>
      <ul><li>Home</li><li>Shop</li><li>About Me</li><li>Photo Wall</li><li>Contact Us</li><li>Cart</li></ul></nav>
    <div class="hero-copy"><h1>Under Morning Lantern</h1><p>Faith-made tees for every day. Wear your light with bold designs and soft fabric.</p><span class="btn">Shop Now</span></div>
  </header>
  <section class="best">
    <h2 class="section-title">Best Sellers</h2>
    <div class="shirts">
      <div class="shirt"><div class="shirt-img" role="img" aria-label="White tee" style="background:var(--shirt-white)"></div><p>Lantern Tee<br>$24.00</p><div class="stars">★★★★★</div></div>
      <div class="shirt"><div class="shirt-img" role="img" aria-label="Purple tee" style="background:var(--shirt-purple)"></div><p>Dawn Tee<br>$24.00</p><div class="stars">★★★★★</div></div>
      <div class="shirt"><div class="shirt-img" role="img" aria-label="Teal tee" style="background:var(--shirt-teal)"></div><p>Morning Tee<br>$24.00</p><div class="stars">★★★★★</div></div>
      <div class="shirt"><div class="shirt-img" role="img" aria-label="Yellow tee" style="background:var(--shirt-yellow)"></div><p>Glow Tee<br>$24.00</p><div class="stars">★★★★★</div></div>
      <div class="shirt"><div class="shirt-img" role="img" aria-label="Orange tee" style="background:var(--shirt-orange)"></div><p>Ember Tee<br>$24.00</p><div class="stars">★★★★★</div></div>
    </div>
  </section>
  <section class="banner" role="img" aria-label="Photo: man wearing a teal tee">
    <div class="banner-copy"><h3>New Designs Every Season</h3><p>Fresh prints made to share the message with a bold look.</p><span class="btn btn--light">Shop Now</span></div>
  </section>
  <section class="features">
    <div class="feature"><svg viewBox="0 0 10 10"><rect x="1" y="3" width="5" height="4"/><path d="M6 4h2l1 2v1H6"/></svg><b>Fast Shipping</b><span>Ships in 3 days</span></div>
    <div class="feature"><svg viewBox="0 0 10 10"><circle cx="5" cy="5" r="4"/><path d="M3 5l1.5 1.5L7 4"/></svg><b>Quality Cotton</b><span>Soft and durable</span></div>
    <div class="feature"><svg viewBox="0 0 10 10"><circle cx="5" cy="5" r="4"/><path d="M5 3v2l1.5 1"/></svg><b>All Sales Final</b><span>No returns</span></div>
    <div class="feature"><svg viewBox="0 0 10 10"><rect x="1.5" y="2.5" width="7" height="5"/><path d="M1.5 4h7"/></svg><b>Secure Payment</b><span>Safe checkout</span></div>
  </section>
  <section class="video" role="img" aria-label="Video still: man in a black printed tee">
    <div class="about-card"><h3>About Me</h3><p>A short story about why these shirts were made and the hope behind each design.</p><span class="btn">Watch Video</span></div>
    <div class="play"><svg viewBox="0 0 24 24"><path d="M10 7l7 5-7 5z" fill="#222"/></svg></div>
  </section>
  <section class="product">
    <span class="arrow" style="left:12px">‹</span><span class="arrow" style="right:12px">›</span>
    <div class="product-img"><div role="img" aria-label="Black tee with print"></div></div>
    <div class="details"><h3>Black T-Shirt</h3><div class="price">$24.00</div><div class="stars">★★★★★</div>
      <p>Soft cotton tee with our lantern print. Unisex fit, made to last.</p>
      <div class="sizes"><span>S</span><span>M</span><span>L</span><span>XL</span><span>2XL</span></div>
      <div class="qty"><span>- 1 +</span></div><span class="btn btn--wide">Add to Cart</span>
      <div class="share">Share <i></i><i></i><i></i><i></i></div></div>
  </section>
  <section class="insta">
    <div class="insta-item"><div class="insta-img" role="img" aria-label="Photo wall post: man in tee" style="background:#6b6f74"></div><p>Sunday best in black.</p></div>
    <div class="insta-item"><div class="insta-img" role="img" aria-label="Photo wall post: teal tee" style="background:#4f8b92"></div><p>Teal for the summer.</p></div>
    <div class="insta-item"><div class="insta-img" role="img" aria-label="Photo wall post: grey tee" style="background:#8a8d90"></div><p>Grey on the go.</p></div>
    <div class="insta-item"><div class="insta-img" role="img" aria-label="Photo wall post: red tee" style="background:#b8574a"></div><p>New ember drop.</p></div>
  </section>
  <footer class="footer">
    <div class="footer-cols"><div class="brand"><i></i>UML</div>
      <div><h4>Pages</h4><ul><li>About Me</li><li>Shop</li><li>Photo Wall</li><li>Contact Us</li></ul></div>
      <div><h4>Help</h4><ul><li>Track Order</li><li>Shipping</li><li>All Sales Final</li></ul></div>
      <div><h4>Mailing List</h4><div class="signup"><span>Your email</span><b>Join</b></div></div></div>
    <div class="social"><i></i><i></i><i></i></div>
    <div class="payments"><span>Palo</span><span>Birch Pay</span><span>Wayfarer</span></div>
    <p class="final">© Under Morning Lantern. All sales final.</p>
  </footer>
  <div class="overlay"></div>
  <div class="login">
    <h2>Login</h2>
    <label>Email</label><div class="field"></div>
    <label>Password</label><div class="field"></div>
    <span class="btn">Sign In</span>
    <p>Forgot password? · Create account</p>
  </div>
</div>

</body>
</html>
```